Verdel Harvest - Stationery Design Project

We need a stationary for our business. We grow roots and fruits in Central and South America, we import and distribute in FL, USA. We do fresh and frozen products.

Target Market(s)

Small and big supermarkets, wholesalers, traders, distributors, etc

Industry/Entity Type

Business

```html
<!DOCTYPE html>
<html lang="en">
<head>
<meta charset="utf-8">
<title>Verdel Harvest – Stationery</title>
<link rel="stylesheet" href="https://fonts.googleapis.com/css2?family=Raleway:wght@500;600&display=swap">
<style>
  :root {
    --bg: #ececec;
    --paper: #ffffff;
    --sage: #98a285;
    --apricot: #f2b466;
    --brand-orange: #e8820e;
    --brand-green: #4e5a2a;
    --edge: #dcdcdc;
  }
  * { margin: 0; padding: 0; box-sizing: border-box; }
  html, body { width: 1200px; height: 1000px; overflow: hidden; }
  body { background: var(--bg); font-family: "Raleway", sans-serif; position: relative; }

  .sheet { position: absolute; background: var(--paper); border: 1px solid var(--edge); overflow: hidden; }
  .sheet svg.swoosh { position: absolute; left: 0; top: 0; width: 100%; height: 100%; }

  .folder { left: 190px; top: 107px; width: 385px; height: 544px; }
  .letterhead { left: 633px; top: 122px; width: 377px; height: 529px; }
  .envelope-back { left: 183px; top: 698px; width: 392px; height: 193px; }
  .envelope-front { left: 633px; top: 697px; width: 392px; height: 193px; }

  .wordmark {
    position: absolute; color: var(--brand-orange); font-weight: 600;
    letter-spacing: 0.02em; white-space: nowrap; line-height: 1;
  }
  .folder .wordmark { left: 0; right: 0; top: 255px; text-align: center; font-size: 31px; }
  .letterhead .wordmark { left: 30px; top: 38px; font-size: 12.5px; }
  .envelope-front .wordmark { left: 254px; top: 37px; font-size: 12.5px; }

  .contact {
    position: absolute; left: 282px; top: 25px; padding-left: 12px;
    border-left: 1px solid var(--brand-green); list-style: none;
  }
  .contact li {
    font-size: 5px; color: var(--brand-green); line-height: 8.5px; white-space: nowrap;
    display: flex; align-items: center; gap: 5px;
  }
  .contact li::before {
    content: ""; width: 4px; height: 4px; border-radius: 50%; background: var(--brand-green);
  }
</style>
</head>
<body>

  <section class="sheet folder" aria-label="Presentation folder">
    <svg class="swoosh" viewBox="0 0 385 544" preserveAspectRatio="none" aria-hidden="true">
      <path d="M0,0 H280 C180,20 80,28 0,28 Z" fill="var(--sage)"/>
      <path d="M0,32 C120,40 270,20 370,0 H385 V4 C270,35 120,56 0,52 Z" fill="var(--apricot)"/>
      <path d="M0,544 C120,498 280,468 385,505 V520 C280,488 130,510 42,544 Z" fill="var(--apricot)"/>
      <path d="M105,544 C220,510 320,514 385,538 V544 Z" fill="var(--sage)"/>
    </svg>
    <div class="wordmark">VERDEL HARVEST</div>
  </section>

  <section class="sheet letterhead" aria-label="Letterhead">
    <svg class="swoosh" viewBox="0 0 377 529" preserveAspectRatio="none" aria-hidden="true">
      <path d="M0,529 C120,483 270,452 377,490 V506 C270,474 130,496 40,529 Z" fill="var(--apricot)"/>
      <path d="M102,529 C215,495 315,500 377,522 V529 Z" fill="var(--sage)"/>
    </svg>
    <div class="wordmark">VERDEL HARVEST</div>
    <ul class="contact">
      <li>0400555012</li>
      <li>0400555034</li>
      <li>www.verdelharvest.com</li>
      <li>support@verdelharvest.com</li>
    </ul>
  </section>

  <section class="sheet envelope-back" aria-label="Envelope back">
    <svg class="swoosh" viewBox="0 0 392 193" preserveAspectRatio="none" aria-hidden="true">
      <path d="M0,0 Q196,140 392,0 Z" fill="var(--apricot)"/>
      <path d="M0,193 Q196,50 392,193 Z" fill="var(--apricot)"/>
    </svg>
  </section>

  <section class="sheet envelope-front" aria-label="Envelope front">
    <svg class="swoosh" viewBox="0 0 392 193" preserveAspectRatio="none" aria-hidden="true">
      <path d="M15,193 C130,150 290,115 392,150 V166 C290,135 140,160 50,193 Z" fill="var(--apricot)"/>
      <path d="M118,193 C230,160 330,162 392,183 V193 Z" fill="var(--sage)"/>
    </svg>
    <div class="wordmark">VERDEL HARVEST</div>
  </section>

</body>
</html>
```